Family business needs stationery redesign with new logo

Family owned company, established in 1987 wanting a brand 'refresh'. We are an electrical, refrigeration and construction company based in the Barkly Region Northern Territory, Australia. We have a new logo we would like to use which is uploaded along with our current letterhead and email signature. We are also dropping the word 'contractors' so please do not include this on any designs. Please note also, the 'orange' color used in our logo and designs should be Northern Territory red ochre which is as follows:

RGB (Hex): #C75B12
PantoneĀ® 159 C
CMYK: 1 / 74 / 100 / 7

We are needing our stationery redesigned using our new logo. Please include letterheads, business cards, envelopes, and email signatures.

We currently use our business letterheads for quotations, invoices, letters, HR matters, and internal memos.

We also need a separate simplified letterhead for internal paperwork such as employee leave forms, meeting agendas, and meeting minutes etc.

Reason: Needing more submissions of full package designs. We are wanting all our stationery, including business cards, letterheads, email signatures, envelopes, etc to be cohesive. We also require ALL the information, as supplied on our template letterhead, to be included on the new letterhead designs. including electrical license no.etc Thank you, R&W

Reason: needing more time as work has got in the way of looking over designs. A lot of designs not meeting the brief/criteria.

Industry/Entity Type

Business

Colors
0355a3
f37122

Requirements
Must have
• The 'orange' color used in the designs should be Northern Territory red ochre which is as follows:
• RGB (Hex): #C75B12
• PantoneĀ® 159 C
• CMYK: 1 / 74 / 100 / 7
• ***MUST INCLUDE ALL INFORMATION THAT IS ON OUR CURRENT LETTERHEAD***
Should not have
• Please do not include the word 'contractors'

```html
<!DOCTYPE html>
<html lang="en">
<head>
<meta charset="utf-8">
<title>R&amp;W Stationery Suite</title>
<link href="https://fonts.googleapis.com/css2?family=Arimo:wght@400;700&family=Tinos&display=swap" rel="stylesheet">
<style>
:root{
  --navy:#1b316e;
  --ochre:#c75b12;
  --paper:#ffffff;
  --bg:#e9eaec;
  --ink:#333333;
  --sans:'Arimo',Arial,sans-serif;
  --serif:'Tinos','Times New Roman',serif;
}
*{margin:0;padding:0;box-sizing:border-box}
html,body{width:1200px;height:938px;overflow:hidden;background:var(--bg)}
.canvas{position:relative;width:1200px;height:938px}
.sheet{position:absolute;background:var(--paper);overflow:hidden}
.wave{position:absolute;left:0;bottom:0;width:100%;display:block}
.brand-name{font-family:var(--sans);font-weight:700;color:var(--navy);line-height:1;letter-spacing:.5px}
.services{font-family:var(--serif);color:var(--navy);line-height:1.2}
.url{position:absolute;font-family:var(--sans);color:#fff;letter-spacing:2.5px}

/* letterhead */
.letterhead{left:184px;top:68px;width:386px;height:544px}
.letterhead .brand{position:absolute;left:18px;top:28px;display:flex;align-items:center;gap:14px}
.letterhead .brand-name{font-size:27px}
.letterhead .services{font-size:8px}
.contact{position:absolute;right:18px;top:22px;text-align:right;font-family:var(--sans);font-size:4.4px;line-height:7.6px;color:#222}
.contact .gap{margin-bottom:5px}
.letter{position:absolute;left:38px;top:138px;width:296px;font-family:var(--sans);font-size:5.2px;line-height:8.6px;color:var(--ink)}
.letter p{margin-bottom:9px}
.letter .tight{margin-bottom:0}
.letter strong{font-weight:700}
.signature{width:40px;height:26px;background:linear-gradient(90deg,#d8d8d8,#efefef);margin:4px 0 8px}

/* folder */
.folder{left:637px;top:42px;width:457px;height:574px}
.folder .brand{position:absolute;left:0;top:232px;width:100%;text-align:center}
.folder .brand-name{font-size:54px}
.folder .services{font-size:15.5px;margin-top:12px}
.folder .url{left:22px;bottom:10px;font-size:10px}

/* business cards */
.card{width:176px;height:98px;border-radius:6px}
.card-front{left:46px;top:660px}
.card-front .brand{position:absolute;left:7px;top:13px;display:flex;align-items:center;gap:6px}
.card-front .brand-name{font-size:15px}
.card-front .services{font-size:4.6px}
.card-front .person{position:absolute;left:102px;top:16px;font-family:var(--sans);color:#222}
.card-front .person-name{font-size:5.6px;letter-spacing:.4px}
.card-front .role{font-size:3.8px;margin-bottom:5px}
.card-front .lines{font-size:3.3px;line-height:5.3px}
.card-front .address{position:absolute;left:10px;bottom:7px;font-family:var(--sans);font-size:4px;line-height:7px;color:#fff}
.card-back{left:46px;top:786px;height:99px}
.card-back .brand{position:absolute;left:42px;top:36px;display:flex;align-items:center;gap:6px}
.card-back .brand-name{font-size:17px}
.card-back .services{font-size:4.8px}

/* envelopes */
.envelope{width:432px;height:207px}
.envelope-front{left:266px;top:674px}
.envelope-front .brand{position:absolute;left:16px;top:22px;display:flex;align-items:center;gap:18px}
.envelope-front .brand-name{font-size:26px}
.envelope-front .services{font-size:8.6px}
.envelope-front .url{left:14px;bottom:9px;font-size:8.6px}
.envelope-back{left:737px;top:672px;height:208px}
.flap{position:absolute;left:0;top:0;width:100%;height:72px;background:var(--ochre);border-radius:0 0 44px 44px}
.flap .url{left:0;width:100%;top:29px;text-align:center;font-size:10.6px}
</style>
</head>
<body>
<div class="canvas">

  <!-- Letterhead -->
  <section class="sheet letterhead">
    <div class="brand">
      <span class="brand-name">R&amp;W</span>
      <div class="services">Electrical<br>Refrigeration<br>Building Services</div>
    </div>
    <div class="contact">
      <div class="gap">14 Station Rd, Unit 2<br>Tennant Creek NT</div>
      <div>08 8962 1040 &#9742;</div>
      <div>08 8962 1041 &#9647;</div>
      <div>08 8962 1042 &#9113;</div>
      <div>info@rwservices.net &#9993;</div>
      <div>www.rwservices.net &#9675;</div>
    </div>
    <div class="letter">
      <p>July 2, 2012</p>
      <p><strong>Dear KL,</strong><br>Harbour House, Lane St., Darwin NT</p>
      <p>is simply dummy text of the printing and typesetting industry. Lorem Ipsum has been the industry's standard dummy text ever since the 1500s, when an unknown printer took a galley of type and scrambled it to make a type specimen book. It has survived not only five centuries, but also the leap into electronic typesetting, remaining essentially unchanged. It was popularised in the 1960s with the release of Letraset sheets containing Lorem Ipsum passages, and more recently with desktop publishing software like Aldus PageMaker including versions of Lorem Ipsum.</p>
      <p style="margin-bottom:26px">is simply dummy text of the printing and typesetting industry. Lorem Ipsum has been the industry's standard dummy text ever since the 1500s, when an unknown printer took a galley of type and scrambled it to make</p>
      <p>is simply dummy text of the printing and typesetting industry. Lorem Ipsum has been the industry's standard dummy text ever since the 1500s, when an unknown printer took a galley of type and scrambled it to make a type specimen book. It has survived not only five centuries, but also the leap into electronic typesetting, remaining essentially unchanged. It was popularised in the 1960s with the release of Letraset sheets containing Lorem Ipsum passages, and more recently with desktop publishing software like Aldus PageMaker including versions of Lorem Ipsum.</p>
      <p class="tight">Best Regards,</p>
      <div class="signature" role="img" aria-label="Handwritten signature"></div>
      <p class="tight"><strong>Daniel Reyes</strong><br>Director</p>
      <p>Harbour House, Lane St., Darwin NT</p>
    </div>
    <svg class="wave" viewBox="0 0 400 80" height="72" preserveAspectRatio="none" aria-hidden="true">
      <path d="M0,42 C70,14 150,40 240,62 C320,80 370,56 400,24 L400,80 L0,80Z" fill="var(--navy)"/>
      <path d="M22,26 C90,6 160,36 250,54 C330,70 375,44 400,14" fill="none" stroke="var(--ochre)" stroke-width="3.5"/>
    </svg>
  </section>

  <!-- Presentation folder -->
  <section class="sheet folder">
    <div class="brand">
      <div class="brand-name">R&amp;W</div>
      <div class="services">Electrical<br>Refrigeration<br>Building Services</div>
    </div>
    <svg class="wave" viewBox="0 0 400 80" height="92" preserveAspectRatio="none" aria-hidden="true">
      <path d="M0,36 C70,8 150,38 240,60 C320,78 370,52 400,20 L400,80 L0,80Z" fill="var(--navy)"/>
      <path d="M24,20 C90,0 160,32 250,52 C330,68 375,38 400,2" fill="none" stroke="var(--ochre)" stroke-width="3.5"/>
    </svg>
    <div class="url">www.rwservices.net</div>
  </section>

  <!-- Business card front -->
  <section class="sheet card card-front">
    <div class="brand">
      <span class="brand-name">R&amp;W</span>
      <div class="services">Electrical<br>Refrigeration<br>Building Services</div>
    </div>
    <div class="person">
      <div class="person-name">MARK ELLISON</div>
      <div class="role">Managing Director</div>
      <div class="lines">
        &#9742; 08 8962 1040<br>
        &#9647; 08 8962 1041<br>
        &#9113; 08 8962 1042<br>
        &#9993; info@rwservices.net<br>
        &#9675; www.rwservices.net
      </div>
    </div>
    <svg class="wave" viewBox="0 0 400 80" height="36" preserveAspectRatio="none" aria-hidden="true">
      <path d="M0,30 C70,6 150,34 240,56 C320,76 370,52 400,22 L400,80 L0,80Z" fill="var(--navy)"/>
      <path d="M24,16 C90,0 160,30 250,48 C330,66 375,40 400,8" fill="none" stroke="var(--ochre)" stroke-width="4"/>
    </svg>
    <div class="address">14 Station Rd, Unit 2<br>Tennant Creek NT</div>
  </section>

  <!-- Business card back -->
  <section class="sheet card card-back">
    <div class="brand">
      <span class="brand-name">R&amp;W</span>
      <div class="services">Electrical<br>Refrigeration<br>Building Services</div>
    </div>
  </section>

  <!-- Envelope front -->
  <section class="sheet envelope envelope-front">
    <div class="brand">
      <span class="brand-name">R&amp;W</span>
      <div class="services">Electrical<br>Refrigeration<br>Building Services</div>
    </div>
    <svg class="wave" viewBox="0 0 400 80" height="68" preserveAspectRatio="none" aria-hidden="true">
      <path d="M0,40 C70,14 150,38 240,58 C320,76 370,54 400,24 L400,80 L0,80Z" fill="var(--navy)"/>
      <path d="M22,24 C90,6 160,34 250,52 C330,68 375,42 400,10" fill="none" stroke="var(--ochre)" stroke-width="3.5"/>
    </svg>
    <div class="url">www.rwservices.net</div>
  </section>

  <!-- Envelope back -->
  <section class="sheet envelope envelope-back">
    <div class="flap"><div class="url">www.rwservices.net</div></div>
  </section>

</div>
</body>
</html>
```